Hybrid Seed corn and Soybean Sales business needs a website.

We here at "KW Grain" feel that we need a website to show a very professional side to our customer base. Although no actual ordering will take place on this website, we would like to put Plot and field trail data on the website. Along with a brief page for each of our hybrids and a place for customers to sign up for a newsletter. The company we sell hybrids for is MolvanGrain.com... Im not sure how this process works as far as myself updating the information or having the data actually put on the website, but feel free to contact me if you need the information. I will attach the logo for the company, (KW Grain).

Target Market(s)

Farmers, "Producers", Corn and soybean production

Industry/Entity Type

Business

Coding

Coded - Design and coding required

Number of Pages Required

5+ page

Colors
f78f20
ffffff

Requirements
Nice to have
• Similar layout to http://www.molvangrain.com/
• And it would be nice to incorporate our story into the website
• http://www.molvangrain.com/our-story/molvan-today/

```html
<!DOCTYPE html>
<html lang="en">
<head>
<meta charset="utf-8">
<title>KW Grain — Hybrid Seed Corn &amp; Soybean</title>
<link href="https://fonts.googleapis.com/css2?family=Lato:ital,wght@0,400;0,700;0,900;1,400&family=Arimo:wght@400;700&family=Raleway:wght@300;400&display=swap" rel="stylesheet">
<style>
:root{
  --orange:#e8830f;
  --orange-light:#f79a2a;
  --orange-dark:#cf6f06;
  --brown:#5b3a24;
  --ink:#3a3a3a;
  --muted:#6b6b6b;
  --cream:#f7f5e8;
  --card:#efe8c9;
  --card-border:#e4dcb6;
  --footer:#252525;
  --white:#ffffff;
}
*{box-sizing:border-box;margin:0;padding:0}
html,body{width:1200px;height:2222px;overflow:hidden;background:var(--white)}
body{position:relative;font-family:"Arimo",Arial,sans-serif;color:var(--ink)}
.abs{position:absolute}

/* header */
.site-header{position:absolute;left:0;top:0;width:1200px;height:133px;border-top:4px solid var(--orange)}
.brand{position:absolute;left:0;width:1200px;top:40px;display:flex;justify-content:center;align-items:center;gap:12px}
.brand-dot{width:40px;height:40px;border-radius:50%;background:var(--orange)}
.brand-name{font-family:"Lato",sans-serif;font-weight:900;font-size:34px;color:var(--brown);letter-spacing:1px}

.main-nav{position:absolute;left:0;top:133px;width:1200px;height:55px;
  background:linear-gradient(#f59a2c,#e07b0c);border-bottom:2px solid #f4b565}
.main-nav a{position:absolute;top:0;height:53px;line-height:53px;text-align:center;color:var(--white);
  font-family:"Lato",sans-serif;font-size:14px;text-decoration:none;border-right:1px solid rgba(255,255,255,.25)}
.main-nav a.active{background:#3b3b3b}

/* hero */
.hero{position:absolute;left:0;top:190px;width:1200px;height:457px;
  background:linear-gradient(180deg,#c9a15a 0%,#a98a4e 22%,#4f6a2e 45%,#6f8a2c 70%,#4d6a22 100%)}
.hero-arrow{position:absolute;top:398px;width:42px;height:42px;border-radius:50%;border:2px solid rgba(255,255,255,.85);background:rgba(0,0,0,.15)}
.hero-title{position:absolute;left:0;width:1200px;top:390px;text-align:center;font-family:"Lato",sans-serif;
  font-weight:900;font-size:92px;color:var(--white);letter-spacing:1px;text-shadow:0 3px 6px rgba(0,0,0,.35)}
.hero-sub{position:absolute;left:0;width:1200px;top:500px;text-align:center;font-family:"Lato",sans-serif;
  font-style:italic;font-size:18px;line-height:33px;color:var(--white);text-shadow:0 1px 3px rgba(0,0,0,.5)}

/* product cards */
.product-card{position:absolute;top:689px;width:283px;height:333px;background:var(--card);border:1px solid var(--card-border);text-align:center}
.product-icon{width:110px;height:110px;margin:22px auto 0;border-radius:8px}
.product-title{margin-top:21px;font-family:"Lato",sans-serif;font-weight:700;font-size:21px;color:var(--brown)}
.product-title span{color:var(--orange)}
.product-text{margin:18px 24px 0;font-size:11.5px;line-height:21px;color:var(--muted)}
.btn-more{display:inline-block;margin-top:18px;width:113px;height:36px;line-height:36px;background:var(--orange);
  color:var(--white);font-family:"Lato",sans-serif;font-weight:700;font-size:13px;border-bottom:2px solid var(--orange-dark)}

/* about */
.about{position:absolute;left:0;top:1061px;width:1200px;height:364px;background:var(--cream);border-top:2px solid #e6e2cd;border-bottom:2px solid #e6e2cd}
.section-title{font-family:"Lato",sans-serif;font-weight:700;font-size:22px;color:var(--brown)}
.section-title span{color:var(--orange)}
.about .section-title{position:absolute;left:99px;top:50px}
.about-lead{position:absolute;left:99px;top:86px;font-family:"Lato",sans-serif;font-style:italic;font-size:15px;color:var(--brown)}
.about-text{position:absolute;left:99px;top:122px;width:540px;font-size:11.5px;line-height:21px;color:var(--muted)}
.about-text p+p{margin-top:21px}
.video{position:absolute;left:680px;top:47px;width:421px;height:271px;background:#1c1c1c}
.video-bar{height:30px;line-height:30px;padding-left:14px;background:#222;color:#ddd;font-size:12px}
.video-screen{position:absolute;left:0;top:30px;width:421px;height:218px;background:radial-gradient(ellipse at 50% 85%,#f0a43a 0%,#b2521a 35%,#5a1d0c 75%,#2a0c06 100%)}
.video-play{position:absolute;left:186px;top:115px;width:50px;height:50px;border-radius:50%;border:3px solid var(--white);background:rgba(255,255,255,.15)}
.video-controls{position:absolute;left:0;bottom:0;width:421px;height:23px;background:#111;border-top:3px solid #555}

/* recent posts */
.recent-title{position:absolute;left:0;top:1458px;width:1200px;text-align:center}
.recent-intro{position:absolute;left:220px;top:1493px;width:760px;text-align:center;font-size:11.5px;line-height:21px;color:var(--muted)}
.post-image{position:absolute;top:1560px;width:166px;height:147px}
.post{position:absolute;top:1558px;width:300px}
.post-title{font-family:"Lato",sans-serif;font-size:14px;color:var(--ink)}
.post-date{margin-top:8px;font-family:"Lato",sans-serif;font-style:italic;font-size:14px;color:var(--orange)}
.post-text{margin-top:10px;font-size:11.5px;line-height:21px;color:var(--muted)}
.post-link{display:block;margin-top:4px;font-size:13px;color:var(--orange);text-decoration:none}
.divider{position:absolute;left:99px;top:1753px;width:1002px;height:1px;background:#ececec}

/* partners */
.partner{position:absolute;top:1788px;width:227px;height:133px;border:4px solid #eeeeee;background:var(--white);display:flex;align-items:center;justify-content:center}
.partner-badge{width:150px;height:56px;border-radius:6px;background:#e3e3e3}

/* newsletter */
.newsletter{position:absolute;left:0;top:1958px;width:1200px;height:89px;background:var(--orange)}
.newsletter-label{position:absolute;left:249px;top:26px;font-family:"Raleway",sans-serif;font-weight:300;font-size:26px;color:var(--white)}
.newsletter-input{position:absolute;left:526px;top:29px;width:358px;height:37px;border-radius:19px;background:var(--white);
  padding-left:20px;line-height:37px;font-family:"Raleway",sans-serif;font-size:13px;color:#555}
.newsletter-btn{position:absolute;left:904px;top:29px;width:146px;height:37px;border-radius:19px;background:#db7408;
  text-align:center;line-height:37px;font-family:"Raleway",sans-serif;font-size:14px;color:var(--white)}

/* footer */
.site-footer{position:absolute;left:0;top:2047px;width:1200px;height:175px;background:var(--footer)}
.social{position:absolute;top:24px;width:35px;height:35px;border-radius:50%;border:1.5px solid #cfcfcf}
.footer-nav{position:absolute;left:0;top:84px;width:1200px;text-align:center;font-size:11.5px;color:var(--white)}
.footer-nav a{color:var(--white);text-decoration:none}
.footer-nav span{margin:0 15px}
.copyright{position:absolute;left:0;top:123px;width:1200px;text-align:center;font-size:11.5px;color:var(--white)}
</style>
</head>
<body>

<header class="site-header">
  <div class="brand"><span class="brand-dot"></span><span class="brand-name">KW GRAIN</span></div>
</header>

<nav class="main-nav">
  <a class="active" style="left:99px;width:119px">HOME</a>
  <a style="left:218px;width:142px">ABOUT US</a>
  <a style="left:360px;width:151px">PRODUCTS</a>
  <a style="left:511px;width:147px">SERVICES</a>
  <a style="left:658px;width:124px">VIDEOS</a>
  <a style="left:782px;width:163px">NEWSLETTER</a>
  <a style="left:945px;width:166px;border-right:none">CONTACT US</a>
</nav>

<section class="hero" role="img" aria-label="Sunset over rows of young soybean plants with a tree line and farmhouse">
</section>
<span class="hero-arrow" style="left:46px"></span>
<span class="hero-arrow" style="left:1112px"></span>
<svg class="abs" style="left:56px;top:408px" width="22" height="22" viewBox="0 0 22 22"><path d="M14 4 L6 11 L14 18 Z" fill="#fff"/></svg>
<svg class="abs" style="left:1122px;top:408px" width="22" height="22" viewBox="0 0 22 22"><path d="M8 4 L16 11 L8 18 Z" fill="#fff"/></svg>
<h1 class="hero-title">KW GRAIN</h1>
<p class="hero-sub">It is a long established fact that a reader will be distracted by the readable content of a page<br>when looking at its layout.</p>

<article class="product-card" style="left:135px">
  <div class="product-icon" role="img" aria-label="Three ears of wheat illustration" style="background:linear-gradient(#f0a33b,#6b3b24)"></div>
  <h2 class="product-title"><span>HYBRID</span> SEEDS</h2>
  <p class="product-text">It is a long established fact that a reader will be distracted by the readable content of a page when making it look like readable English</p>
  <span class="btn-more">MORE INFO</span>
</article>
<article class="product-card" style="left:459px">
  <div class="product-icon" role="img" aria-label="Ear of corn illustration" style="background:linear-gradient(135deg,#f0a33b,#6b3b24)"></div>
  <h2 class="product-title"><span>CORN</span></h2>
  <p class="product-text">It is a long established fact that a reader will be distracted by the readable content of a page when making it look like readable English</p>
  <span class="btn-more">MORE INFO</span>
</article>
<article class="product-card" style="left:781px">
  <div class="product-icon" role="img" aria-label="Soybean pods illustration" style="background:linear-gradient(#7a4a2c,#e8941f)"></div>
  <h2 class="product-title"><span>SOY</span>BEAN</h2>
  <p class="product-text">It is a long established fact that a reader will be distracted by the readable content of a page when making it look like readable English</p>
  <span class="btn-more">MORE INFO</span>
</article>

<section class="about">
  <h2 class="section-title"><span>ABOUT OUR</span> KW GRAIN</h2>
  <p class="about-lead">Neque porro quisquam est qui dolorem ipsum quia dolor</p>
  <div class="about-text">
    <p>It is a long established fact that a reader will be distracted by the readable content of a page when looking at its layout. The point of using Lorem Ipsum is that it has a more-or-less normal distribution of letters, as opposed to using 'Content here, content here', making it look like readable English. Many desktop publishing packages and web page editors now use Lorem Ipsum as their default model text, and a search for 'lorem ipsum' will uncover many web sites still in their infancy</p>
    <p>Distribution of letters, as opposed to using 'Content here, content here', making it look like readable English. Many desktop publishing packages and web page editors now use Lorem Ipsum as their default model text, and a search for 'lorem ipsum' will uncover many web sites still in their infancy......</p>
  </div>
  <div class="video">
    <div class="video-bar">KW GRAIN</div>
    <div class="video-screen" role="img" aria-label="Video still of a field at sunset"></div>
    <span class="video-play"></span>
    <svg class="abs" style="left:204px;top:130px" width="20" height="20" viewBox="0 0 20 20"><path d="M4 2 L17 10 L4 18 Z" fill="#fff"/></svg>
    <div class="video-controls"></div>
  </div>
</section>

<h2 class="section-title recent-title"><span>RECENT</span> POSED</h2>
<p class="recent-intro">It is a long established fact that a reader will be distracted by the readable content of a page when looking at its layout. The point of using Lorem Ipsum is that 'Content here, content here', making it look like readable English.</p>

<div class="post-image" style="left:99px;background:linear-gradient(135deg,#8b6a45,#7fb032 55%,#5b8a22)" role="img" aria-label="Green soybean pods on a wooden table"></div>
<article class="post" style="left:286px">
  <h3 class="post-title">Contrary to popular belief</h3>
  <p class="post-date">25 Mar 2015</p>
  <p class="post-text">Distribution of letters, as opposed to using 'Content here, content here', making it look like readable English. Many desktop publishing packages and web page editors now many web sites still in their infancy......</p>
  <a class="post-link">Read More</a>
</article>

<div class="post-image" style="left:631px;background:linear-gradient(#6b7a86,#9aa39a 40%,#4f7a2a 60%,#3d6420)" role="img" aria-label="Rows of crops under a cloudy sky"></div>
<article class="post" style="left:819px">
  <h3 class="post-title">Contrary to popular belief</h3>
  <p class="post-date">25 Mar 2015</p>
  <p class="post-text">Distribution of letters, as opposed to using 'Content here, content here', making it look like readable English. Many desktop publishing packages and web page editors now many web sites still in their infancy......</p>
  <a class="post-link">Read More</a>
</article>

<div class="divider"></div>

<div class="partner" style="left:212px"><span class="partner-badge" role="img" aria-label="Partner badge"></span></div>
<div class="partner" style="left:487px"><span class="partner-badge" role="img" aria-label="Partner badge"></span></div>
<div class="partner" style="left:762px"><span class="partner-badge" role="img" aria-label="Partner badge"></span></div>

<section class="newsletter">
  <span class="newsletter-label">Subscribe Newsletter :</span>
  <span class="newsletter-input">Enter Your Email Id :</span>
  <span class="newsletter-btn">SUBSCRIBE</span>
</section>

<footer class="site-footer">
  <span class="social" style="left:513px" aria-label="Social link"></span>
  <span class="social" style="left:560px" aria-label="Social link"></span>
  <span class="social" style="left:607px" aria-label="Social link"></span>
  <span class="social" style="left:654px" aria-label="Social link"></span>
  <nav class="footer-nav">
    <a>Home</a><span>/</span><a>About Us</a><span>/</span><a>Products</a><span>/</span><a>Services</a><span>/</span><a>Videos</a><span>/</span><a>Newsletter</a><span>/</span><a>Contact Us</a>
  </nav>
  <p class="copyright">© Copy Rights 2015 KW Grain.All Rights Resever.</p>
</footer>

</body>
</html>
```